Fitness Equipment Repair Business Needs a Catchy New Business Card

We have an existing business card, however, it is quite plain and boring. We are expanding primarily in the commercial area (gyms, studios, apartment complexes etc). The business card will serve as eye candy to those managers/owners that can't be met for a face to face.
Originally I was planning for a brochure as well, but all of our information is better summarized on our website. (brightloopservice.ca).
I would like the card to match the colour scheme of the website and utilize the logo. It should have a professional clean feel to it, however, a little colouring outside the lines wouldn't hurt.
The example card is for my service technician (Colin Marsh). If possible I would like to be able to edit the text to use for more than one person.

Industry/Entity Type

Appliance Repair

Contact Information for Business Card

Clean, crisp and professional but needs to be eye catching. Preferably using the black, white and red colour scheme matching the website. Double sided would be nice, but is not necessary.

Colors
ec1f27
ffffff
000000

Requirements
Must have
• Must be able to edit name, phone number and title to use for multiple people. Must show the company website (brightloopservice.ca).

```html
<!DOCTYPE html>
<html lang="en">
<head>
<meta charset="utf-8">
<title>Brightloop Service – Business Card</title>
<link rel="stylesheet" href="https://fonts.googleapis.com/css2?family=Cinzel:wght@400&family=Open+Sans:wght@400;600;700&display=swap">
<style>
  :root {
    --brand-red: #ec1f27;
    --brand-black: #000000;
    --card-dark: #2b2b2b;
    --paper: #ffffff;
    --ink: #1d1d1d;
    --ink-soft: #3a3a3a;
    --stage: #e9e7e4;
  }
  * { box-sizing: border-box; margin: 0; padding: 0; }
  html, body { width: 1200px; height: 900px; overflow: hidden; }
  body {
    background: var(--stage);
    font-family: "Open Sans", Arial, sans-serif;
    position: relative;
  }
  .card {
    position: absolute;
    left: 290px;
    width: 620px;
    height: 354px;
    overflow: hidden;
    box-shadow: 0 6px 18px rgba(0,0,0,.18);
  }
  /* Front */
  .card--front { top: 50px; background: var(--card-dark); color: var(--paper); }
  .card--front .brand-mark {
    position: absolute; left: 150px; top: 46px; width: 96px; height: 96px;
    border: 2px solid var(--paper); border-radius: 50%;
  }
  .card--front .brand-name {
    position: absolute; left: 285px; top: 40px;
    font-family: "Cinzel", "Times New Roman", serif;
    font-size: 38px; line-height: 40px; letter-spacing: 2px; color: var(--paper);
  }
  .tagline {
    position: absolute; left: 0; right: 0; top: 196px; text-align: center;
    font-size: 21px; line-height: 30px; text-transform: uppercase; letter-spacing: .5px;
  }
  /* Back */
  .card--back { top: 480px; background: var(--paper); color: var(--ink); }
  .corner-mark { position: absolute; left: 0; top: 0; }
  .person { position: absolute; left: 78px; top: 24px; }
  .person__name { color: var(--brand-red); font-weight: 700; font-size: 19px; line-height: 22px; }
  .person__title { color: var(--ink-soft); font-size: 13px; line-height: 16px; }
  .contact { position: absolute; left: 34px; top: 96px; font-size: 14.5px; line-height: 20px; color: var(--ink); }
  .contact__address { margin-bottom: 8px; }
  .contact__row { display: flex; align-items: center; gap: 8px; }
  .contact__row svg { width: 12px; height: 12px; flex: none; }
  .card--back .brand-mark {
    position: absolute; left: 300px; top: 112px; width: 76px; height: 76px;
    border: 2px solid var(--ink); border-radius: 50%;
  }
  .card--back .brand-name {
    position: absolute; left: 392px; top: 114px;
    font-family: "Cinzel", "Times New Roman", serif;
    font-size: 27px; line-height: 32px; letter-spacing: 1px; color: var(--ink);
    white-space: nowrap;
  }
  .bands { position: absolute; left: 0; top: 0; }
</style>
</head>
<body>

<section class="card card--front" aria-label="Business card front">
  <div class="brand-mark" aria-hidden="true"></div>
  <div class="brand-name">Brightloop<br>Service</div>
  <p class="tagline">When your equipment can't finish<br>their workout, give us a call!</p>
</section>

<section class="card card--back" aria-label="Business card back">
  <svg class="corner-mark" width="70" height="60" viewBox="0 0 70 60" aria-hidden="true">
    <polygon points="0,0 38,0 0,34" fill="var(--brand-red)"/>
    <polygon points="44,8 64,8 64,48 20,48" fill="var(--brand-black)"/>
  </svg>
  <div class="person">
    <p class="person__name">Colin Marsh</p>
    <p class="person__title">Managing Director</p>
  </div>

  <div class="contact">
    <p class="contact__address">12345, Address Goes Here<br>Country Name, 123456.</p>
    <p class="contact__row">
      <svg viewBox="0 0 12 12" aria-hidden="true"><rect x="3" y="0.5" width="6" height="11" rx="1.2" fill="none" stroke="var(--brand-red)" stroke-width="1.3"/><circle cx="6" cy="9.3" r=".8" fill="var(--brand-red)"/></svg>
      044-123 456 789</p>
    <p class="contact__row">
      <svg viewBox="0 0 12 12" aria-hidden="true"><path d="M2.5 1 L4.5 1 L5.2 3.6 L3.9 4.6 Q5 7 7.4 8.1 L8.4 6.8 L11 7.5 L11 9.5 Q10.5 11 9 11 Q1 10 1 3 Q1 1.5 2.5 1 Z" fill="var(--brand-red)"/></svg>
      044-123 456 789</p>
    <p class="contact__row">
      <svg viewBox="0 0 12 12" aria-hidden="true"><rect x="0.5" y="2" width="11" height="8" fill="var(--brand-red)"/><polyline points="0.5,2.3 6,6.5 11.5,2.3" fill="none" stroke="var(--paper)" stroke-width="1"/></svg>
      info@brightloopservice.ca</p>
    <p class="contact__row">
      <svg viewBox="0 0 12 12" aria-hidden="true"><circle cx="6" cy="6" r="5.5" fill="var(--brand-red)"/><path d="M0.5 6 H11.5 M6 0.5 Q2.5 6 6 11.5 M6 0.5 Q9.5 6 6 11.5" fill="none" stroke="var(--paper)" stroke-width=".8"/></svg>
      www.brightloopservice.ca</p>
  </div>

  <div class="brand-mark" aria-hidden="true"></div>
  <div class="brand-name">Brightloop<br>Service</div>

  <svg class="bands" width="620" height="354" viewBox="0 0 620 354" aria-hidden="true">
    <polygon points="0,244 290,244 276,266 0,266" fill="var(--brand-red)"/>
    <polygon points="312,298 620,298 620,336 290,336" fill="var(--brand-black)"/>
  </svg>
</section>

</body>
</html>
```